Flu Vaccination Poster

I would like a banner designed to display from the ceiling in my pharmacy promoting flu vaccination.
In large words, it should say "Flu Vaccination"
In smaller text it should say "Available here. See in store for details"
It should also display our website kestrelvalepharmacy.com.au and have a message for more information visit the website.
Currently patients required to pay for the service, however in May this year the vaccine will become free for everyone, so I would like to put a sticker on the sign in May saying "FREE" and then remove the sticker when no longer free. The banner dimensions are "2.19m wide x 0.61m tall.
I have uploaded logo files plus a photo of a previously used banner which is no longer relevant. More formats of logo files are available if required.

```html
<!DOCTYPE html>
<html lang="en">
<head>
<meta charset="utf-8">
<title>Flu Vaccination Ceiling Banner</title>
<link rel="stylesheet" href="https://fonts.googleapis.com/css2?family=Figtree:wght@400;500;700;800;900&display=swap">
<style>
  :root {
    --stage: #e6e7e9;
    --paper: #ffffff;
    --navy: #243a64;
    --sub-blue: #1d5ea8;
    --sky: #b9d6ec;
    --pink: #d81b67;
    --white: #ffffff;
  }
  * { box-sizing: border-box; margin: 0; padding: 0; }
  html, body {
    width: 1200px; height: 754px; overflow: hidden;
    background: var(--stage);
    font-family: "Figtree", Arial, sans-serif;
  }
  .banner {
    position: absolute;
    left: 97px; width: 1004px; height: 279px;
    background: var(--paper);
    overflow: visible;
  }
  .banner--logo { top: 63px; }
  .banner--plain { top: 398px; }

  .headline {
    position: absolute; left: 44px; top: 32px;
    width: 920px;
    display: flex; justify-content: space-between; align-items: baseline;
    color: var(--navy);
    font-size: 106px; line-height: 1;
    letter-spacing: -1px;
    white-space: nowrap;
  }
  .headline__strong { font-weight: 900; letter-spacing: -3px; }
  .headline__light { font-weight: 500; letter-spacing: 1px; }

  .subline {
    position: absolute; left: 0; right: 0; top: 136px;
    text-align: center;
    color: var(--sub-blue);
    font-size: 45px; font-weight: 400; letter-spacing: -1.2px;
    line-height: 1;
  }
  .subline strong { font-weight: 800; letter-spacing: -1.8px; }

  .info-band {
    position: absolute; left: 0; right: 0; bottom: 0; height: 69px;
    background: var(--navy);
  }
  .info-band__edge {
    position: absolute; left: 0; top: -4px; width: 100%; height: 6px;
  }
  .info-band__text {
    position: absolute; left: 193px; top: 19px;
    color: var(--sky);
    font-size: 26px; font-weight: 700; letter-spacing: -0.7px;
    line-height: 1; white-space: nowrap;
  }
  .info-band__dot { color: var(--pink); margin: 0 10px; }

  .store-name {
    position: absolute; left: 24px; top: 20px;
    display: flex; align-items: center; gap: 6px;
    color: var(--white);
    font-size: 15px; font-weight: 700; line-height: 1.05;
  }
  .store-name__mark {
    width: 11px; height: 11px; border-radius: 50%;
    background: var(--pink); flex: none;
  }

  .free-badge {
    position: absolute; top: 152px; width: 84px; height: 113px;
  }
  .free-badge--right { left: 893px; }
  .free-badge--left { left: 40px; }
  .free-badge svg { position: absolute; inset: 0; }
  .free-badge__text {
    position: absolute; left: 0; right: 0; top: 52px;
    text-align: center; color: var(--white);
    font-size: 27px; font-weight: 900; line-height: 0.85;
    letter-spacing: -1px;
  }
</style>
</head>
<body>

<section class="banner banner--logo">
  <h1 class="headline"><span class="headline__strong">FLU</span><span class="headline__light">VACCINATION</span></h1>
  <p class="subline">Available here. <strong>See in store</strong> for details</p>
  <div class="info-band">
    <svg class="info-band__edge" viewBox="0 0 1004 6" preserveAspectRatio="none" aria-hidden="true">
      <polygon fill="var(--navy)" points="0,3 60,2 130,4 210,1 300,3 390,2 470,4 560,1 650,3 740,2 830,4 920,1 1004,3 1004,6 0,6"/>
    </svg>
    <div class="store-name"><span class="store-name__mark"></span><span>Kestrel Vale<br>Pharmacy</span></div>
    <p class="info-band__text">For More Details<span class="info-band__dot">•</span>www.kestrelvalepharmacy.com.au</p>
  </div>
  <div class="free-badge free-badge--right">
    <svg viewBox="0 0 84 113" aria-hidden="true">
      <path fill="var(--pink)" d="M42 0 C54 20 84 46 84 71 A42 42 0 0 1 0 71 C0 46 30 20 42 0 Z"/>
      <line x1="20" y1="48" x2="40" y2="34" stroke="var(--white)" stroke-width="2.5" stroke-linecap="round"/>
      <path fill="var(--white)" d="M52 30 C55 35 57 38 57 40 A5 5 0 0 1 47 40 C47 38 49 35 52 30 Z"/>
    </svg>
    <div class="free-badge__text">FREE<br>MAY</div>
  </div>
</section>

<section class="banner banner--plain">
  <h1 class="headline"><span class="headline__strong">FLU</span><span class="headline__light">VACCINATION</span></h1>
  <p class="subline">Available here. <strong>See in store</strong> for details</p>
  <div class="info-band">
    <svg class="info-band__edge" viewBox="0 0 1004 6" preserveAspectRatio="none" aria-hidden="true">
      <polygon fill="var(--navy)" points="0,3 60,2 130,4 210,1 300,3 390,2 470,4 560,1 650,3 740,2 830,4 920,1 1004,3 1004,6 0,6"/>
    </svg>
    <p class="info-band__text">For More Details<span class="info-band__dot">•</span>www.kestrelvalepharmacy.com.au</p>
  </div>
  <div class="free-badge free-badge--left">
    <svg viewBox="0 0 84 113" aria-hidden="true">
      <path fill="var(--pink)" d="M42 0 C54 20 84 46 84 71 A42 42 0 0 1 0 71 C0 46 30 20 42 0 Z"/>
      <line x1="20" y1="48" x2="40" y2="34" stroke="var(--white)" stroke-width="2.5" stroke-linecap="round"/>
      <path fill="var(--white)" d="M52 30 C55 35 57 38 57 40 A5 5 0 0 1 47 40 C47 38 49 35 52 30 Z"/>
    </svg>
    <div class="free-badge__text">FREE<br>MAY</div>
  </div>
</section>

</body>
</html>
```